Food broker, trader, wholesaler, liquidator looking for a 5 pages website

Looking for a 5 pages website design. We are food brokers, traders, wholesaler and closeout buyer working with manufacturers, distributors, importers sell to retailers, food service operators and industrial (ingredients). We help market their products. We are a resource for those who need a solution in the distribution/selling/placement of food on the shelves, kitchens and pantries. Whether we open new accounts with new products or sell short dated inventory, we know where to go and get results.

Target Market(s)

Food manufacturers, food distributors, food brokers

Coding

Coded - Design and coding required

Number of Pages Required

4 page

Font styles to use
Serif

Requirements
Must have
• Food-food production-warehouse-Food packaging-people meeting-trucks-supermarket shelves-

```html
<!DOCTYPE html>
<html lang="en">
<head>
<meta charset="utf-8">
<title>Harbor Provision Co. — Food Brokers &amp; Traders</title>
<link rel="stylesheet" href="https://fonts.googleapis.com/css2?family=Noticia+Text:wght@400;700&family=Raleway:wght@400;500&display=swap">
<style>
  :root {
    --navy: #0c0c5a;
    --navy-deep: #0a0a4e;
    --ink: #2b2b2b;
    --muted: #555;
    --white: #fff;
    --footer: #222;
    --line: #d8d8d8;
    --serif: "Noticia Text", Georgia, serif;
    --sans: "Raleway", Arial, sans-serif;
  }
  * { box-sizing: border-box; margin: 0; padding: 0; }
  html, body { width: 1200px; height: 3617px; overflow: hidden; }
  body { position: relative; background: var(--white); font-family: var(--serif); color: var(--ink); }
  .abs { position: absolute; }

  /* Header */
  .site-header { position: absolute; top: 0; left: 0; width: 1200px; height: 108px; background: var(--white); z-index: 3; }
  .brand-badge { position: absolute; left: 111px; top: -20px; width: 200px; height: 200px; border-radius: 50%; background: var(--white); display: flex; align-items: center; justify-content: center; text-align: center; z-index: 4; }
  .brand-badge span { font-family: var(--serif); font-weight: 700; color: var(--navy); font-size: 17px; line-height: 1.25; margin-top: -10px; }
  .main-nav a { position: absolute; top: 46px; font-size: 14px; color: var(--navy); text-decoration: none; font-family: var(--serif); }
  .main-nav a.active { border-bottom: 1px solid var(--navy); padding-bottom: 2px; }

  /* Hero */
  .hero { position: absolute; top: 108px; left: 0; width: 1200px; height: 706px; overflow: hidden;
    background: linear-gradient(180deg, #3b5fae 0%, #6f8fcf 35%, #b7c2dc 58%, #6a6a88 75%, #3b3e5c 100%); }
  .hero-curve { position: absolute; left: 0; top: 0; }
  .hero-title { position: absolute; left: 671px; top: 182px; font-size: 47px; color: var(--white); font-weight: 400; }
  .hero-text { position: absolute; left: 668px; top: 255px; width: 430px; font-size: 17px; line-height: 37px; color: #eef1fb; }
  .btn-solid { position: absolute; background: var(--navy); color: var(--white); font-family: var(--serif); display: flex; align-items: center; justify-content: center; border-radius: 3px; }
  .hero .btn-solid { left: 671px; top: 383px; width: 131px; height: 48px; font-size: 16px; }

  /* Section headings */
  .section-title { position: absolute; left: 0; width: 1200px; text-align: center; font-size: 39px; color: var(--navy); font-weight: 400; }
  .section-sub { position: absolute; left: 0; width: 1200px; text-align: center; font-size: 15px; color: var(--ink); }

  /* Process */
  .process { position: absolute; left: 0; top: 940px; }
  .process text { font-family: var(--serif); font-size: 19px; fill: var(--ink); }

  /* About */
  .about { position: absolute; top: 1663px; left: 0; width: 1200px; height: 484px; background: var(--navy-deep); overflow: hidden; }
  .about h2 { position: absolute; left: 139px; top: 72px; font-size: 46px; font-weight: 400; color: var(--white); }
  .about .rule { position: absolute; left: 139px; top: 139px; width: 60px; height: 3px; background: var(--white); }
  .about p { position: absolute; left: 139px; top: 170px; width: 468px; font-size: 12.5px; line-height: 30px; color: var(--white); text-align: justify; }
  .btn-outline { position: absolute; left: 139px; top: 376px; width: 131px; height: 48px; border: 1px solid var(--white); color: var(--white); font-size: 14px; display: flex; align-items: center; justify-content: center; border-radius: 2px; }
  .about-photo { position: absolute; right: 0; top: 0; }

  /* Services */
  .service-card { position: absolute; top: 2311px; width: 309px; height: 391px; background: var(--white); border: 1px solid #e6e6e6; box-shadow: 0 0 6px rgba(0,0,0,.08); text-align: center; }
  .service-card .photo { position: absolute; left: 10px; top: 9px; width: 289px; height: 215px; }
  .service-card h3 { position: absolute; top: 253px; width: 100%; font-size: 19px; font-weight: 400; color: var(--ink); }
  .service-card .rule { position: absolute; top: 289px; left: 133px; width: 42px; height: 2px; background: var(--navy); }
  .service-card p { position: absolute; top: 309px; left: 20px; width: 269px; font-family: var(--sans); font-size: 13px; line-height: 25px; color: var(--muted); }

  /* Contact */
  .contact { position: absolute; top: 2762px; left: 0; width: 1200px; height: 480px;
    background: linear-gradient(180deg, #f2f2f4 0%, #ecebe9 50%, #e9e5e2 100%); }
  .field { position: absolute; background: var(--white); border: 1px solid #cfcfcf; font-size: 12px; color: #555; padding: 0 15px; display: flex; align-items: center; }
  .field.area { align-items: flex-start; padding-top: 14px; }

  /* Footer */
  .site-footer { position: absolute; top: 3242px; left: 0; width: 1200px; height: 375px; background: var(--footer); color: var(--white); font-family: var(--sans); }
  .footer-badge { position: absolute; left: 169px; top: 88px; width: 140px; height: 110px; border-radius: 50%; background: var(--white); }
  .footer-name { position: absolute; left: 100px; top: 196px; width: 280px; text-align: center; font-family: var(--serif); font-weight: 700; font-size: 18px; }
  .footer-col h4 { position: absolute; font-family: var(--serif); font-weight: 400; font-size: 23px; top: 46px; }
  .footer-list { position: absolute; top: 112px; list-style: none; font-size: 14px; }
  .footer-list li { height: 35px; }
  .footer-list li::before { content: "»"; display: inline-block; width: 28px; }
  .newsletter p { position: absolute; left: 836px; top: 100px; width: 260px; font-size: 14px; line-height: 25px; }
  .newsletter .field { left: 836px; top: 168px; width: 250px; height: 42px; border: none; font-family: var(--sans); font-size: 14px; color: #333; }
  .newsletter .btn-solid { left: 836px; top: 216px; width: 95px; height: 40px; font-family: var(--sans); font-size: 14px; border-radius: 0; }
  .footer-divider { position: absolute; left: 112px; top: 299px; width: 976px; height: 1px; background: #3a3a3a; }
  .copyright { position: absolute; top: 327px; width: 1200px; text-align: center; font-size: 13px; }
</style>
</head>
<body>

<header class="site-header">
  <div class="brand-badge"><span>HARBOR<br>PROVISION CO.</span></div>
  <nav class="main-nav">
    <a class="active" style="left:584px">Home</a>
    <a style="left:671px">About Us</a>
    <a style="left:779px">What we do</a>
    <a style="left:907px">Contact</a>
    <a style="left:1006px">Giving Back</a>
  </nav>
</header>

<section class="hero">
  <div class="abs" role="img" aria-label="Cargo ship loaded with containers at a harbor under a blue evening sky" style="inset:0;"></div>
  <svg class="hero-curve" width="1200" height="706" viewBox="0 0 1200 706">
    <path d="M0,580 Q600,830 1200,566 L1200,706 L0,706 Z" fill="#fff"/>
  </svg>
  <h1 class="hero-title">Harbor Provision Co.</h1>
  <p class="hero-text">Sed ut perspiciatis unde omnis iste natus error sit voluptatem accusantium doloremque laudantium, totam rem aperiam</p>
  <a class="btn-solid">Read More</a>
</section>

<h2 class="section-title" style="top:845px">Our Process</h2>
<p class="section-sub" style="top:913px">Sed ut perspiciatis unde omnis iste natus error sit voluptatem accusantium doloremque</p>

<svg class="process" width="1200" height="723" viewBox="0 940 1200 723">
  <defs>
    <marker id="arrowhead" viewBox="0 0 12 12" refX="10" refY="6" markerWidth="12" markerHeight="12" orient="auto">
      <path d="M1,1 L11,6 L1,11" fill="none" stroke="#0c0c5a" stroke-width="1.3"/>
    </marker>
  </defs>
  <g fill="none" stroke="#0c0c5a" stroke-width="3" marker-end="url(#arrowhead)">
    <path d="M622,1043 Q680,1045 722,1070"/>
    <path d="M820,1158 Q850,1200 860,1252"/>
    <path d="M860,1382 Q850,1440 810,1480"/>
    <path d="M708,1558 Q640,1588 562,1583"/>
    <path d="M446,1535 Q405,1510 380,1464"/>
    <path d="M332,1352 Q325,1290 338,1234"/>
    <path d="M405,1123 Q450,1085 499,1063"/>
  </g>
  <g fill="#fff" stroke="#0c0c5a" stroke-width="2">
    <circle cx="556" cy="1050" r="54"/>
    <circle cx="770" cy="1114" r="54"/>
    <circle cx="858" cy="1315" r="54"/>
    <circle cx="762" cy="1523" r="54"/>
    <circle cx="505" cy="1565" r="54"/>
    <circle cx="342" cy="1416" r="54"/>
    <circle cx="362" cy="1176" r="54"/>
  </g>
  <g fill="none" stroke="#0c0c5a" stroke-width="2">
    <!-- production machine -->
    <rect x="536" y="1030" width="40" height="30" rx="2"/><circle cx="562" cy="1045" r="7"/><line x1="542" y1="1060" x2="542" y2="1074"/><line x1="534" y1="1074" x2="552" y2="1074"/>
    <!-- warehouse -->
    <path d="M746,1100 L770,1088 L794,1100 L794,1138 L746,1138 Z"/><rect x="756" y="1114" width="28" height="24"/><line x1="756" y1="1122" x2="784" y2="1122"/>
    <!-- packaged food -->
    <rect x="840" y="1300" width="36" height="36" rx="3"/><rect x="845" y="1290" width="26" height="10"/><path d="M848,1318 Q858,1310 868,1318 Q858,1326 848,1318 Z"/>
    <!-- people -->
    <circle cx="762" cy="1506" r="7"/><circle cx="746" cy="1514" r="5"/><circle cx="778" cy="1514" r="5"/><path d="M748,1544 L748,1526 Q762,1514 776,1526 L776,1544"/><path d="M736,1544 L736,1528 Q742,1522 748,1526"/><path d="M788,1544 L788,1528 Q782,1522 776,1526"/>
    <!-- truck -->
    <rect x="478" y="1548" width="32" height="28"/><path d="M510,1556 L524,1556 L532,1566 L532,1576 L510,1576"/><circle cx="488" cy="1580" r="5"/><circle cx="522" cy="1580" r="5"/>
    <!-- shelves -->
    <rect x="318" y="1394" width="48" height="44"/><line x1="318" y1="1409" x2="366" y2="1409"/><line x1="318" y1="1424" x2="366" y2="1424"/><line x1="330" y1="1394" x2="330" y2="1438"/><line x1="348" y1="1394" x2="348" y2="1438"/>
    <!-- food bowl -->
    <path d="M336,1180 L388,1180 Q384,1202 362,1204 Q340,1202 336,1180 Z"/><path d="M346,1178 Q362,1156 378,1178"/><path d="M354,1150 Q350,1142 356,1136"/><path d="M366,1150 Q362,1142 368,1136"/>
  </g>
  <text x="394" y="1002">Food</text><text x="394" y="1036">Production</text>
  <text x="842" y="1117">Warehouse</text>
  <text x="928" y="1309">Food</text><text x="928" y="1343">Packaging</text>
  <text x="834" y="1521">People</text><text x="834" y="1555">Meeting</text>
  <text x="378" y="1586">Trucks</text>
  <text x="153" y="1416">Supermarket</text><text x="153" y="1450">Shelves</text>
  <text x="244" y="1177">Food</text>
</svg>

<section class="about">
  <svg class="about-photo" width="530" height="484" viewBox="0 0 530 484" role="img" aria-label="Smiling warehouse manager holding a clipboard between stocked shelves">
    <defs>
      <linearGradient id="warehouseTone" x1="0" y1="0" x2="1" y2="1">
        <stop offset="0" stop-color="#b9b4aa"/><stop offset=".5" stop-color="#8d95a8"/><stop offset="1" stop-color="#5c5f6e"/>
      </linearGradient>
    </defs>
    <path d="M110,0 Q-40,242 110,484 L530,484 L530,0 Z" fill="url(#warehouseTone)"/>
  </svg>
  <h2>About Us</h2>
  <div class="rule"></div>
  <p>Harbor Provision Co. works with food manufacturers, brand owners, distributors and wholesalers market their products. Retail, Food Service and Industrial ingredients. Founded in 2008, Harbor Provision Co. started with the distribution of gluten free products understanding the need to provide access to unique flavors and products for the celiac consumers. From this, we expanded into deli, dairy, groceries, frozen and beverages.</p>
  <a class="btn-outline">READ MORE</a>
</section>

<h2 class="section-title" style="top:2190px">What We Do</h2>
<p class="section-sub" style="top:2252px">Sed ut perspiciatis unde omnis iste natus error sit voluptatem accusantium doloremque</p>

<article class="service-card" style="left:112px">
  <div class="photo" role="img" aria-label="Business team meeting in a glass-walled office with sales charts on screen" style="background:linear-gradient(135deg,#2c3442,#6d7a8a 60%,#c9d3cf);"></div>
  <h3>Sales &amp; Marketing</h3><div class="rule"></div>
  <p>we connect food buyers and sellers through a dedicated approach.</p>
</article>
<article class="service-card" style="left:446px">
  <div class="photo" role="img" aria-label="Hands typing on a laptop beside trading screens" style="background:linear-gradient(135deg,#3a4a5c,#7b8ea0 50%,#c7a57e);"></div>
  <h3>Trading</h3><div class="rule"></div>
  <p>we purchase goods anywhere and ship them Nationwide and Export.</p>
</article>
<article class="service-card" style="left:779px">
  <div class="photo" role="img" aria-label="Two warehouse workers checking a cardboard box and a tablet" style="background:linear-gradient(135deg,#6b625a,#9aa3ad 55%,#c4b59c);"></div>
  <h3>Closeout/Excess Inventory</h3><div class="rule"></div>
  <p>we buy closeouts and excess inventory for prisons, outlet stores and discounters.</p>
</article>

<section class="contact" role="img" aria-label="Faded warehouse interior in the background">
  <h2 class="section-title" style="top:48px">Contact Us</h2>
  <p class="section-sub" style="top:107px">Sed ut perspiciatis unde omnis iste natus error sit voluptatem accusantium</p>
  <div class="field" style="left:281px;top:161px;width:314px;height:44px">First Name :</div>
  <div class="field" style="left:606px;top:161px;width:313px;height:44px">Last Name :</div>
  <div class="field" style="left:281px;top:218px;width:314px;height:44px">Email :</div>
  <div class="field" style="left:606px;top:218px;width:313px;height:44px">Phone :</div>
  <div class="field area" style="left:281px;top:272px;width:638px;height:87px">Message :</div>
  <a class="btn-solid" style="left:526px;top:382px;width:147px;height:48px;font-size:14px;border-radius:0">SUBMIT</a>
</section>

<footer class="site-footer">
  <div class="footer-badge"></div>
  <div class="footer-name">HARBOR PROVISION CO.</div>
  <div class="footer-col"><h4 style="left:396px">Quick Links</h4></div>
  <ul class="footer-list" style="left:396px">
    <li>Home</li><li>About Us</li><li>What we do</li><li>Contact</li><li>Giving Back</li>
  </ul>
  <div class="footer-col"><h4 style="left:613px">Services</h4></div>
  <ul class="footer-list" style="left:613px">
    <li>Sed ut perspiciatis</li><li>unde omnis iste</li><li>natus error sit</li><li>voluptatem</li><li>accusantium</li>
  </ul>
  <div class="footer-col newsletter">
    <h4 style="left:836px">Newsletter</h4>
    <p>Sed ut perspiciatis unde omnis iste natus error sit voluptatem</p>
    <div class="field">Email :</div>
    <a class="btn-solid">SUBMIT</a>
  </div>
  <div class="footer-divider"></div>
  <p class="copyright">© Copyright 2020 Harbor Provision Co. All Rights Reserved</p>
</footer>

</body>
</html>
```